Eye Catching Email Marketing design

Our health care consulting firm is based in New York City. We sell health care consulting Services to medical practices (doctors). We need a powerful email marketing design to use as one of our primary selling tools to attract new clients. The Design should convey health care knowledge, expertise professionalism, cutting edge technology and the services we offer. <br/>The design should incorporate our logo and its colors (blue and white) but we want it to be eye catching and vibrant, so other colors be included. We are open to the designer's creativity. Any pictures used should show diversity (races)and should include women. Designers can find our logo and other graphics on our website at www harbor ridge advisory.com. Please feel free to ask questions.<br/><br/>

Target Market(s)

Health care professionals, executives and Doctors.

Colors

Designer to choose colors to be used in the design.

Requirements
Nice to have
• What ever the design feels will help make this design vibrant

```html
<!DOCTYPE html>
<html lang="en">
<head>
<meta charset="utf-8">
<title>Harbor Ridge Advisory – Newsletter</title>
<link href="https://fonts.googleapis.com/css2?family=Montserrat:wght@300;400;500;600;700&display=swap" rel="stylesheet">
<style>
:root{
  --orange:#f77f00;
  --sky:#31a5d6;
  --navy:#0a57a8;
  --ink-blue:#2f6fa8;
  --white:#ffffff;
  --rule-peach:#e9b999;
  --rule-grey:#9fb3c8;
  --rule-sky:#a9d6ec;
}
*{margin:0;padding:0;box-sizing:border-box}
html,body{width:1200px;height:2652px;overflow:hidden;background:var(--white)}
body{font-family:'Montserrat',sans-serif}
.stage{position:absolute;left:0;top:0;width:1168px;height:2581px;transform:scale(1.02740);transform-origin:0 0}
.abs{position:absolute}
.photo{position:absolute}
.center{text-align:center}
/* top contact bar */
.contact{position:absolute;top:7px;font-size:9px;color:var(--orange);white-space:nowrap}
.contact svg{vertical-align:-1px;margin-right:2px}
.top-rule{position:absolute;left:348px;top:28px;width:469px;height:1px;background:var(--sky)}
.brand{position:absolute;left:340px;top:48px;width:485px;text-align:center;color:var(--navy);font-weight:600;font-size:15px;letter-spacing:.5px}
.brand .mark{display:inline-block;width:14px;height:14px;background:var(--navy);border-radius:50%;vertical-align:-2px;margin-right:8px}
.brand small{display:block;font-size:9px;font-weight:600;letter-spacing:1px;margin-top:3px}
/* blocks */
.block{position:absolute}
.bg-orange{background:var(--orange)}
.bg-sky{background:var(--sky)}
.bg-navy{background:var(--navy)}
.btn{position:absolute;background:var(--white);color:var(--orange);font-size:11px;display:flex;align-items:center;justify-content:center}
.btn.blue-text{color:var(--sky)}
.btn.filled{background:var(--sky);color:var(--white)}
.hero-title{position:absolute;left:340px;width:485px;top:345px;text-align:center;color:var(--white);font-size:18px;font-weight:400;letter-spacing:.3px}
.rule{position:absolute;height:1px}
.body-w{color:var(--white);font-size:11px;line-height:16px}
.body-b{color:var(--ink-blue);font-size:11px;line-height:16px}
.h-white{color:var(--white);font-weight:500;font-size:19px}
.checklist{list-style:none;font-size:11px;line-height:21.3px;color:var(--white)}
.service{position:absolute;top:1520px;width:120px;text-align:center;color:var(--white);font-size:11px;font-weight:700;line-height:13px;letter-spacing:-.3px}
.service svg{display:block;margin:0 auto 14px}
.card-text{position:absolute;top:1791px;width:150px;text-align:center;color:var(--white);font-size:11px;line-height:13px}
.social{position:absolute;top:2504px;width:24px;height:24px;border:1.5px solid var(--white);border-radius:50%}
.footer-links{position:absolute;left:340px;width:485px;top:2549px;text-align:center;color:var(--white);font-size:9px}
</style>
</head>
<body>
<div class="stage">

  <!-- contact bar -->
  <div class="contact" style="left:370px"><svg width="6" height="8" viewBox="0 0 6 8"><path d="M3 0a3 3 0 0 1 3 3c0 2-3 5-3 5S0 5 0 3a3 3 0 0 1 3-3z" fill="#f77f00"/></svg>Your Address</div>
  <div class="contact" style="left:476px"><svg width="8" height="6" viewBox="0 0 8 6"><rect x=".5" y=".5" width="7" height="5" fill="none" stroke="#f77f00"/><path d="M.5.5 4 3.5 7.5.5" fill="none" stroke="#f77f00"/></svg>info@example.com</div>
  <div class="contact" style="left:598px"><svg width="8" height="6" viewBox="0 0 8 6"><rect x=".5" y=".5" width="7" height="5" fill="none" stroke="#f77f00"/></svg>www.example.com</div>
  <div class="contact" style="left:733px"><svg width="8" height="7" viewBox="0 0 8 7"><path d="M0 2q4-3 8 0v1H6V2H2v1H0zM1 4h6v3H1z" fill="#f77f00"/></svg>+1 234 56789</div>
  <div class="top-rule"></div>

  <div class="brand"><span class="mark"></span>HARBOR RIDGE ADVISORY<small>HARBOR RIDGE ADVISORY LLC</small></div>

  <!-- hero -->
  <div class="photo" role="img" aria-label="Diverse team of doctors and executives meeting at a table in a bright corridor" style="left:340px;top:98px;width:485px;height:235px;background:linear-gradient(120deg,#d9dcdf,#eef0f1 55%,#c9c3bd)"></div>
  <div class="block bg-orange" style="left:340px;top:333px;width:485px;height:171px"></div>
  <div class="hero-title">ADVANCING HEALTHCARE OPERATIONS</div>
  <div class="rule" style="left:493px;top:379px;width:180px;background:#fbbf80"></div>
  <p class="abs body-w center" style="left:370px;width:425px;top:391px">Lorem ipsum dolor sit amet, consectetur adipiscing elit, sed do eiusmod tempor incididunt ut labore et dolore magna aliqua.</p>
  <div class="btn" style="left:538px;top:437px;width:89px;height:33px">Read More</div>

  <!-- welcome -->
  <div class="photo" role="img" aria-label="Smiling woman doctor with a tablet, flanked by two colleagues" style="left:340px;top:504px;width:242px;height:296px;background:linear-gradient(160deg,#dfe4e6,#f2f3f3 50%,#c8cdd0)"></div>
  <div class="abs" style="left:590px;top:553px;color:var(--sky);font-size:24px;font-weight:400">Welcome</div>
  <div class="abs" style="left:590px;top:588px;width:230px;color:var(--orange);font-size:22px;font-weight:500;line-height:26px">Harbor Ridge Advisory</div>
  <p class="abs body-b" style="left:590px;top:647px;width:225px">Lorem ipsum dolor sit amet, consectetur adipiscing elit, sed do eiusmod tempor incididunt ut labore et dolore magna.</p>
  <div class="btn filled" style="left:591px;top:710px;width:88px;height:31px">Read More</div>
  <div class="rule" style="left:418px;top:811px;width:328px;background:var(--rule-peach)"></div>

  <!-- sky + corridor -->
  <div class="block bg-sky" style="left:340px;top:823px;width:243px;height:249px"></div>
  <div class="abs h-white" style="left:357px;top:870px">Lorem Ipsum</div>
  <p class="abs body-w" style="left:355px;top:909px;width:215px">Lorem ipsum dolor sit amet, consectetur adipiscing elit, sed do eiusmod tempor incididunt ut labore et dolore magna.</p>
  <div class="btn blue-text" style="left:416px;top:988px;width:90px;height:33px">Read More</div>
  <div class="photo" role="img" aria-label="Long bright hospital corridor with medical staff" style="left:583px;top:823px;width:242px;height:249px;background:linear-gradient(90deg,#c5ccd1,#eef1f2 50%,#9fb0bb)"></div>

  <!-- nurse + checklist -->
  <div class="photo" role="img" aria-label="Smiling woman surgeon in scrubs with a stethoscope" style="left:340px;top:1072px;width:242px;height:295px;background:linear-gradient(180deg,#f3f3f4 40%,#8fa3dc)"></div>
  <div class="block bg-orange" style="left:582px;top:1072px;width:243px;height:295px"></div>
  <div class="abs h-white center" style="left:582px;width:243px;top:1108px">Lorem Ipsum</div>
  <ul class="abs checklist" style="left:624px;top:1147px">
    <li>✓ Lorem ipsum dolor sit amet</li>
    <li>✓ Lorem ipsum dolor sit amet</li>
    <li>✓ Lorem ipsum dolor sit amet</li>
    <li>✓ Lorem ipsum dolor sit amet</li>
  </ul>
  <div class="btn" style="left:659px;top:1248px;width:89px;height:33px">Read More</div>
  <div class="rule" style="left:406px;top:1379px;width:353px;background:var(--rule-grey)"></div>

  <!-- services -->
  <div class="block bg-sky" style="left:340px;top:1392px;width:485px;height:232px"></div>
  <div class="abs h-white center" style="left:340px;width:485px;top:1420px">Lorem Ipsum</div>
  <p class="abs body-w center" style="left:360px;width:445px;top:1459px">Lorem ipsum dolor sit amet, consectetur adipiscing elit, sed do eiusmod tempor incididunt ut labore et dolore magna.</p>
  <div class="rule" style="left:453px;top:1506px;width:259px;background:#bfe3f3"></div>

  <div class="service" style="left:340px">
    <svg width="40" height="44" viewBox="0 0 40 40"><path d="M20 5a15 15 0 0 1 13 7.5M35 20a15 15 0 0 1-7.5 13M20 35A15 15 0 0 1 7 27.5M5 20a15 15 0 0 1 7.5-13" fill="none" stroke="#fff" stroke-width="4"/><path d="M30 7l4 6-7 1zM33 29l-6 4-1-7zM10 33l-4-6 7-1zM7 11l6-4 1 7z" fill="#fff"/></svg>
    REVENUE CYCLE<br>MANAGEMENT</div>
  <div class="service" style="left:462px">
    <svg width="40" height="44" viewBox="0 0 40 40"><path d="M8 4h20v28a4 4 0 0 1-4 4H12a4 4 0 0 0 4-4V8H8z" fill="#fff"/><path d="M18 14h10v8c0 5-5 7-5 7s-5-2-5-7z" fill="#31a5d6"/><path d="M20 20l2 2 4-4" fill="none" stroke="#fff" stroke-width="2"/></svg>
    COMPLIANCE<br>MANAGEMENT</div>
  <div class="service" style="left:583px">
    <svg width="40" height="44" viewBox="0 0 40 40"><circle cx="20" cy="12" r="6" fill="none" stroke="#fff" stroke-width="4" stroke-dasharray="3 1.7"/><path d="M4 18l4 14 8 4v-8l-6-6M36 18l-4 14-8 4v-8l6-6" fill="#fff"/></svg>
    HEALTHCARE<br>INNOVATION</div>
  <div class="service" style="left:705px">
    <svg width="40" height="44" viewBox="0 0 40 40"><circle cx="20" cy="14" r="10" fill="none" stroke="#fff" stroke-width="4" stroke-dasharray="4 2"/><circle cx="20" cy="14" r="5" fill="#fff"/><path d="M8 26h24v8H8z" fill="#fff"/><path d="M14 30h12" stroke="#31a5d6" stroke-width="2"/></svg>
    PRACTICE<br>MANAGEMENT</div>

  <!-- cards -->
  <div class="block bg-navy" style="left:340px;top:1640px;width:485px;height:236px"></div>
  <div class="photo" role="img" aria-label="Dental instruments on a tray" style="left:348px;top:1651px;width:146px;height:117px;background:linear-gradient(150deg,#e8ebee,#c9d0d6)"></div>
  <div class="photo" role="img" aria-label="Surgical team operating under theatre lights" style="left:510px;top:1651px;width:146px;height:117px;background:linear-gradient(160deg,#4f6277,#1e3550)"></div>
  <div class="photo" role="img" aria-label="Doctors reviewing scans together" style="left:672px;top:1651px;width:146px;height:117px;background:linear-gradient(140deg,#e6e9ec,#3c6a98)"></div>
  <div class="card-text" style="left:346px">I'm a new Text block ready for your content.</div>
  <div class="card-text" style="left:508px">I'm a new Text block ready for your content.</div>
  <div class="card-text" style="left:670px">I'm a new Text block ready for your content.</div>
  <div class="btn blue-text" style="left:376px;top:1832px;width:89px;height:33px">Read More</div>
  <div class="btn blue-text" style="left:538px;top:1832px;width:89px;height:33px">Read More</div>
  <div class="btn blue-text" style="left:700px;top:1832px;width:89px;height:33px">Read More</div>
  <div class="rule" style="left:406px;top:1888px;width:353px;background:var(--rule-sky)"></div>

  <!-- lab -->
  <div class="block bg-orange" style="left:340px;top:1900px;width:243px;height:280px"></div>
  <div class="abs h-white" style="left:347px;top:1952px">Lorem Ipsum</div>
  <p class="abs body-w" style="left:355px;top:2017px;width:210px">Lorem ipsum dolor sit amet, consectetur adipiscing elit, sed do eiusmod tempor incididunt ut labore dolore magna lorem.</p>
  <div class="photo" role="img" aria-label="Laboratory pipette and sample tubes in a green rack" style="left:583px;top:1900px;width:242px;height:280px;background:linear-gradient(200deg,#f1f2f3 35%,#cfd6d8 60%,#3aa58c)"></div>

  <!-- closing -->
  <div class="photo" role="img" aria-label="Smiling woman doctor in a white coat in an office" style="left:340px;top:2180px;width:242px;height:309px;background:linear-gradient(170deg,#eceae6,#d8d3cc)"></div>
  <div class="abs" style="left:605px;top:2208px;color:var(--orange);font-size:20px;font-weight:400">Lorem ipsum</div>
  <p class="abs body-b" style="left:605px;top:2240px;width:200px;line-height:19px">Lorem ipsum dolor sit amet, consectetur adipiscing elit, sed do eiusmod tempor incididunt ut labore et dolore magna. Sed ut perspiciatis unde omnis iste.</p>
  <div class="abs body-b" style="left:605px;top:2354px">Kind Regards,</div>
  <div class="photo" role="img" aria-label="Handwritten signature" style="left:605px;top:2380px;width:145px;height:60px;background:linear-gradient(90deg,#eef3f8,#f7f9fb)"></div>
  <div class="abs" style="left:605px;top:2446px;color:var(--orange);font-size:11px;font-weight:500">CEO, COMPANY NAME</div>

  <!-- footer -->
  <div class="block bg-navy" style="left:340px;top:2489px;width:485px;height:92px"></div>
  <div class="social" style="left:511px"></div>
  <div class="social" style="left:551px"></div>
  <div class="social" style="left:590px"></div>
  <div class="social" style="left:630px"></div>
  <div class="footer-links">Unsubscribe&nbsp; | &nbsp;View Online</div>

</div>
</body>
</html>
```